New Poster Design for Film Festival

Hi! We need a poster design for our student film festival and the University of Larchmont. We screen over 300 short films over a 3 days in May. Our committee wants a look feel similar to the image we attached below.

Target Market(s)

Students and general audience.

Industry/Entity Type

Festival

Colors
3377b5
85abd2
34b8a4
f68e4e

Requirements
Must have
• Reeds Film Festival
17th Annual
May 2-3-4 2014
Dale Hunworth Cinema
Free Admission
Department of Screen and Digital Narrative

Poster size 36" (high) x 24" (wide)
University of Larchmont
www.reedsfilmfest-example.org
Nice to have
• Bold lettering
Should not have
• Flamingos - hate them :)

```html
<!DOCTYPE html>
<html lang="en">
<head>
<meta charset="utf-8">
<title>Reeds Film Festival 2014</title>
<link rel="stylesheet" href="https://fonts.googleapis.com/css2?family=Black+Ops+One&display=swap">
<style>
  :root {
    --festival-blue: #3177b8;
    --soft-blue: #85abd2;
    --splash-orange: #f68e4e;
    --paper-white: #ffffff;
    --ink-blue: #3a7cb9;
  }
  html, body {
    margin: 0;
    padding: 0;
    width: 900px;
    height: 1200px;
    overflow: hidden;
    background: var(--festival-blue);
  }
  .poster {
    position: relative;
    width: 900px;
    height: 1200px;
    overflow: hidden;
    background: var(--festival-blue);
    font-family: "Black Ops One", "Arial Black", sans-serif;
    text-transform: uppercase;
  }
  .brush-texture,
  .title-splash {
    position: absolute;
    inset: 0;
    width: 900px;
    height: 1200px;
  }
  .tagline {
    position: absolute;
    margin: 0;
    color: var(--soft-blue);
    line-height: 0.95;
    white-space: nowrap;
    transform-origin: left top;
    transform: rotate(14deg);
  }
  .tagline--flat {
    transform: rotate(6deg);
  }
  .annual {
    position: absolute;
    top: 30px;
    left: 170px;
    margin: 0;
    font-size: 76px;
    color: var(--ink-blue);
    letter-spacing: 2px;
    transform: rotate(-2deg);
    white-space: nowrap;
  }
  .title-block {
    position: absolute;
    left: 40px;
    top: 120px;
    width: 860px;
    height: 560px;
    transform: rotate(-21deg);
    transform-origin: center;
  }
  .festival-name {
    position: absolute;
    left: 40px;
    top: 150px;
    margin: 0;
    font-size: 230px;
    line-height: 1;
    color: var(--paper-white);
    letter-spacing: 2px;
    font-weight: 400;
  }
  .festival-sub {
    position: absolute;
    left: 150px;
    top: 385px;
    margin: 0;
    font-size: 78px;
    line-height: 1;
    color: var(--paper-white);
    letter-spacing: 4px;
    font-weight: 400;
  }
  .dates {
    position: absolute;
    top: 815px;
    left: 0;
    width: 900px;
    margin: 0;
    text-align: center;
    font-size: 100px;
    line-height: 1;
    color: var(--paper-white);
    letter-spacing: 2px;
    white-space: nowrap;
  }
  .details {
    position: absolute;
    top: 1050px;
    left: 0;
    width: 900px;
    margin: 0;
    padding: 0;
    list-style: none;
    text-align: center;
    color: var(--paper-white);
    font-size: 20px;
    line-height: 26px;
    letter-spacing: 1px;
    white-space: nowrap;
  }
  .details .web {
    text-transform: none;
  }
</style>
</head>
<body>
<main class="poster">
  <svg class="brush-texture" viewBox="0 0 900 1200" role="img" aria-label="Light blue brush stroke bands sweeping across the background">
    <g fill="var(--soft-blue)">
      <path d="M120 20 Q450 -10 800 60 L790 130 Q450 80 130 110 Z"/>
      <path d="M0 240 Q300 160 620 130 L640 200 Q330 240 20 330 Z"/>
      <path d="M420 520 Q650 480 900 520 L900 600 Q660 560 440 600 Z"/>
      <path d="M0 700 Q250 640 520 700 L510 770 Q260 720 0 780 Z"/>
      <path d="M120 940 Q430 900 900 960 L900 1040 Q430 980 140 1020 Z"/>
      <path d="M0 1140 Q300 1080 620 1120 L600 1200 L0 1200 Z"/>
    </g>
  </svg>

  <p class="tagline" style="top:-10px;left:10px;font-size:34px;">300 Shortfilms<br>during 3 days</p>
  <p class="tagline" style="top:60px;left:770px;font-size:50px;">300 Shortfilms<br>during 3 days</p>
  <p class="tagline" style="top:160px;left:-20px;font-size:56px;">300 Shortfilms<br>during 3 days</p>
  <p class="tagline" style="top:540px;left:690px;font-size:40px;">300 Shortfilms<br>during 3 days</p>
  <p class="tagline" style="top:630px;left:620px;font-size:56px;">300 Shortfilms<br>during 3 days</p>
  <p class="tagline" style="top:650px;left:-20px;font-size:46px;">300 Shortfilms<br>during 3 days</p>
  <p class="tagline tagline--flat" style="top:920px;left:-40px;font-size:40px;">300 Shortfilms<br>during 3 days</p>
  <p class="tagline" style="top:1160px;left:780px;font-size:30px;">300 Shortfilms<br>during 3 days</p>
  <p class="tagline" style="top:1150px;left:-10px;font-size:40px;">300 Shortfilms</p>

  <svg class="title-splash" viewBox="0 0 900 1200" role="img" aria-label="Orange paint splash behind the festival title">
    <path fill="var(--splash-orange)" d="M90 640 L60 470 L210 330 L460 220 L640 130 L760 150 L700 260 L520 360 L350 470 L230 560 Z"/>
  </svg>

  <p class="annual">17th Annual</p>

  <header class="title-block">
    <h1 class="festival-name">Reeds</h1>
    <p class="festival-sub">Film Festival</p>
  </header>

  <p class="dates">May 2.3.4. 2014</p>

  <ul class="details">
    <li>Dale Hunworth Cinema</li>
    <li>Free Admission</li>
    <li>Department of Screen and Digital Narrative</li>
    <li>University of Larchmont</li>
    <li class="web">www.reedsfilmfest-example.org</li>
  </ul>
</main>
</body>
</html>
```